English and Spanish Language School Needs a Business Card

Need a business card design a startup company called Maribel Language School. The company will offer English and Spanish conversational level courses designed to make the learner feel comfortable with grammar and vocabulary. We would like to see a logo with some colour that should communicate learning, growth.

Target Market(s)

Consumers and businesses

Industry/Entity Type

Education

Contact Information for Business Card

TBD

Font styles to use
Serif

Requirements
Must have
• Include the following
• Logo
• Name
• Title
• Cellphone Number
• Office Phone number
• Email address
• Office Address

```html
<!DOCTYPE html>
<html lang="en">
<head>
<meta charset="utf-8">
<title>Maribel Language School – Business Card</title>
<link rel="stylesheet" href="https://fonts.googleapis.com/css2?family=Tinos:wght@400;700&display=swap">
<style>
  :root {
    --card-red: #d4232f;
    --card-red-deep: #c01d29;
    --card-white: #f7f7f7;
    --accent-teal: #1fb5b8;
    --ink-white: #ffffff;
    --stage: #ecebe8;
  }
  * { box-sizing: border-box; margin: 0; padding: 0; }
  html, body { width: 1200px; height: 780px; overflow: hidden; }
  body {
    background: var(--stage);
    font-family: "Tinos", "Times New Roman", serif;
    display: flex;
    align-items: center;
    justify-content: center;
    gap: 40px;
  }
  .card {
    position: relative;
    width: 540px;
    height: 310px;
    overflow: hidden;
    box-shadow: 0 6px 18px rgba(0,0,0,0.18);
  }
  .card-front { background: var(--card-white); }
  .front-shape { position: absolute; inset: 0; }
  .front-logo {
    position: absolute;
    left: 34px;
    top: 118px;
    color: var(--card-red);
    font-weight: 700;
    line-height: 1;
  }
  .front-logo .logo-name { display: block; font-size: 58px; }
  .front-logo .logo-sub { display: block; font-size: 22px; margin-top: 6px; }
  .contact {
    position: absolute;
    right: 28px;
    top: 26px;
    width: 200px;
    color: var(--ink-white);
    text-align: right;
  }
  .contact-name { font-size: 21px; font-weight: 700; letter-spacing: 0.5px; }
  .contact-title { font-size: 14px; margin-bottom: 18px; }
  .contact-line { font-size: 14px; line-height: 1.35; }
  .contact-block { margin-bottom: 14px; }
  .contact-icons {
    position: absolute;
    right: 28px;
    bottom: 22px;
    display: flex;
    gap: 6px;
  }
  .contact-icons svg { width: 18px; height: 18px; }
  .card-back {
    background: radial-gradient(ellipse at 50% 45%, var(--card-red) 0%, var(--card-red-deep) 100%);
    display: flex;
    align-items: center;
    justify-content: center;
  }
  .back-logo {
    color: var(--ink-white);
    font-weight: 700;
    text-align: center;
    line-height: 1;
  }
  .back-logo .logo-name { display: block; font-size: 72px; }
  .back-logo .logo-sub { display: block; font-size: 24px; margin-top: 8px; }
</style>
</head>
<body>
  <section class="card card-front">
    <svg class="front-shape" viewBox="0 0 540 310" preserveAspectRatio="none" aria-hidden="true">
      <path d="M275 0 Q385 150 300 310 L540 310 L540 0 Z" fill="var(--card-red)"/>
      <path d="M262 0 Q370 150 288 310" fill="none" stroke="var(--accent-teal)" stroke-width="4"/>
    </svg>
    <div class="front-logo">
      <span class="logo-name">Maribel</span>
      <span class="logo-sub">Language School</span>
    </div>
    <div class="contact">
      <p class="contact-name">DANIEL REYES</p>
      <p class="contact-title">Manager</p>
      <div class="contact-block">
        <p class="contact-line">Your Address, 2nd Ste</p>
        <p class="contact-line">Lindenford, Texas 1234</p>
      </div>
      <div class="contact-block">
        <p class="contact-line">555 010 2468</p>
        <p class="contact-line">555 010 2469</p>
      </div>
      <p class="contact-line">hello@maribelschool.com</p>
    </div>
    <div class="contact-icons" aria-hidden="true">
      <svg viewBox="0 0 18 18"><rect x="0.5" y="0.5" width="17" height="17" rx="2" fill="none" stroke="#fff"/><path d="M5 4h3l1 3-2 1a7 7 0 0 0 3 3l1-2 3 1v3c-6 0-9-3-9-9z" fill="#fff"/></svg>
      <svg viewBox="0 0 18 18"><rect x="0.5" y="0.5" width="17" height="17" rx="2" fill="none" stroke="#fff"/><rect x="6" y="3" width="6" height="12" rx="1" fill="#fff"/></svg>
      <svg viewBox="0 0 18 18"><rect x="0.5" y="0.5" width="17" height="17" rx="2" fill="none" stroke="#fff"/><rect x="3.5" y="5" width="11" height="8" fill="none" stroke="#fff"/><path d="M3.5 5l5.5 4.5 5.5-4.5" fill="none" stroke="#fff"/></svg>
    </div>
  </section>

  <section class="card card-back">
    <div class="back-logo">
      <span class="logo-name">Maribel</span>
      <span class="logo-sub">Language School</span>
    </div>
  </section>
</body>
</html>
```